WordPress Design for both website and landing page for an expert

I need a clean and stylish design for my new website. I work as an expert (see attached file WHY HOW WHAT), my product is expert opinion (reports) for company evaluations You can use all of the attached pictures colored or black / white. The person is me, you can add other pictures, if you want. The design should be clean and stylish, so you could use white, black, gray, silver and / or one additional color. I have added an idea about my website, see attached file CONCEPT WEBSITE If you have any more information, please do not hesitate to contact us 'Hesitate to ask me ...

```html
<!DOCTYPE html>
<html lang="de">
<head>
<meta charset="utf-8">
<title>Lenz Harward – Sachverständiger für Firmenbewertungen</title>
<link href="https://fonts.googleapis.com/css2?family=Montserrat:wght@300;400;500;600;700&display=swap" rel="stylesheet">
<style>
:root{
  --ink:#1c1c1c;
  --text:#333;
  --muted:#c9c9c9;
  --light:#eeeeee;
  --panel:#ececec;
  --night:#1d2b3d;
  --white:#fff;
}
*{margin:0;padding:0;box-sizing:border-box}
html,body{width:1200px;height:2731px;overflow:hidden}
body{font-family:'Montserrat',Arial,sans-serif;color:var(--text);background:var(--white);position:relative}
.abs{position:absolute}

.site-header{position:absolute;top:0;left:0;width:1200px;height:93px;background:var(--white);box-shadow:0 2px 6px rgba(0,0,0,.12);z-index:2}
.brand{position:absolute;left:173px;top:30px;font-size:20px;font-weight:500;letter-spacing:3px;color:#555;text-transform:uppercase}
.main-nav a{position:absolute;top:40px;font-size:13px;font-weight:500;color:var(--ink);text-decoration:none;letter-spacing:.5px}

.hero{position:absolute;top:93px;left:0;width:1200px;height:539px;background:linear-gradient(90deg,#d8d7d3 0%,#c9c6c0 45%,#a89d92 75%,#8a6e58 100%)}
.hero h1{position:absolute;left:173px;top:168px;font-size:45px;line-height:47px;font-weight:700;color:var(--ink)}
.hero p{position:absolute;left:173px;top:286px;font-size:22px;line-height:30px;font-weight:500;color:var(--ink)}
.slider-dots{position:absolute;left:582px;top:502px;display:flex;gap:4px}
.slider-dots span{width:8px;height:8px;border-radius:50%;background:#888}
.slider-dots span:first-child{background:var(--white);border:1px solid #888}

.reasons h2{position:absolute;top:705px;width:1200px;text-align:center;font-size:36px;font-weight:600;color:var(--ink)}
.reasons .lead{position:absolute;top:762px;width:1200px;text-align:center;font-size:17px;font-weight:500;color:#444}
.connector{position:absolute;top:866px;height:3px;background:var(--ink)}
.reason{position:absolute;top:812px;width:260px;text-align:center}
.reason svg{display:block;margin:0 auto}
.reason .num{font-size:58px;font-weight:300;color:var(--muted);line-height:58px;margin-top:20px}
.reason h3{font-size:19px;font-weight:600;color:var(--ink);margin-top:2px}
.reason p{font-size:12.5px;line-height:20px;margin-top:12px;color:#333}

.faq-photo{position:absolute;top:1184px;left:0;width:592px;height:464px;background:linear-gradient(135deg,#8f8b85 0%,#e3e1dc 40%,#c4c5c7 70%,#6d6f73 100%)}
.faq{position:absolute;top:1184px;left:592px;width:608px;height:464px;background:var(--panel)}
.faq h2{position:absolute;left:44px;top:76px;font-size:35px;font-weight:700;color:var(--ink)}
.faq .body{position:absolute;left:44px;top:136px;width:400px;font-size:12.5px;line-height:20px;color:#333}
.faq .body p{margin-bottom:20px}

.statement{position:absolute;top:1648px;left:0;width:1200px;height:342px;background:linear-gradient(180deg,#1b2536 0%,#26364a 60%,#3a3a3c 100%)}
.statement p{position:absolute;left:200px;width:800px;text-align:center;color:var(--white);font-size:19.5px;line-height:28px}

.promise .brand-mark{position:absolute;top:2090px;width:1200px;text-align:center;font-size:40px;font-weight:700;color:#888;letter-spacing:4px}
.promise h2{position:absolute;top:2204px;width:1200px;text-align:center;font-size:24px;font-weight:600;color:var(--ink)}
.promise p{position:absolute;top:2258px;width:1200px;text-align:center;font-size:15px;line-height:24px;color:#333}

.site-footer{position:absolute;top:2391px;left:0;width:1200px;height:340px;background:var(--light);border-top:5px solid #333}
.site-footer h4{font-size:19px;font-weight:600;color:var(--ink);margin-bottom:12px}
.footer-col{position:absolute;top:60px}
.footer-col li{list-style:none;font-size:13px;line-height:25px;color:#222}
.signup{position:absolute;left:707px;top:97px;width:320px;height:31px;display:flex}
.signup .email{flex:1;background:var(--white);border-radius:16px 0 0 16px;font-size:11px;color:#888;padding:9px 14px}
.signup .btn{width:84px;background:#222;color:var(--white);border-radius:0 16px 16px 0;font-size:12px;font-weight:600;text-align:center;line-height:31px}
.follow{position:absolute;left:707px;top:158px;font-size:19px;font-weight:600;color:var(--ink);display:flex;align-items:center;gap:8px}
.follow .dot{width:26px;height:26px;border-radius:50%;background:#222}
.follow .dot:first-child{margin-left:6px}
.footer-rule{position:absolute;left:173px;top:270px;width:854px;height:1px;background:#d4d4d4}
.copyright{position:absolute;top:300px;width:1200px;text-align:center;font-size:13px;color:#222}
</style>
</head>
<body>

<header class="site-header">
  <div class="brand">Lenz Harward</div>
  <nav class="main-nav">
    <a style="left:419px">HOME</a>
    <a style="left:501px">WHAT I DO</a>
    <a style="left:617px">WHY I DO IT &amp; HOW I DO IT</a>
    <a style="left:841px">ABOUT ME</a>
    <a style="left:958px">CONTACT</a>
  </nav>
</header>

<section class="hero" role="img" aria-label="Portrait photo of the expert in a white shirt leaning on a railing in a bright office">
  <h1>Sachverständiger für<br>Firmenbewertungen</h1>
  <p>Sie benötigen ein Gutachten zur Ermittlung<br>des Wertes Ihres Unternehmens</p>
  <div class="slider-dots"><span></span><span></span><span></span><span></span></div>
</section>

<section class="reasons">
  <h2>Why Choose Us</h2>
  <div class="lead">3 reasons, why you should work with me</div>
  <div class="connector" style="left:386px;width:131px"></div>
  <div class="connector" style="left:679px;width:133px"></div>

  <div class="reason" style="left:170px">
    <svg width="104" height="104" viewBox="0 0 104 104" fill="none" stroke="#1c1c1c" stroke-width="4" stroke-linecap="round">
      <circle cx="52" cy="52" r="47"/><path d="M52 22v30l18 18"/>
      <path d="M52 9v5M52 90v5M9 52h5M90 52h5"/>
    </svg>
    <div class="num">01</div>
    <h3>Schnell</h3>
    <p>Sie bekommen Ihr Gutachten<br>zeitnah (innerhalb von max. 21 Tagen<br>nach Zugang aller benötigten<br>Unterlagen)</p>
  </div>

  <div class="reason" style="left:471px">
    <svg width="104" height="104" viewBox="0 0 104 104" fill="none" stroke="#1c1c1c" stroke-width="4" stroke-linejoin="round" stroke-linecap="round">
      <path d="M52 6L18 16v32c0 24 16 40 34 50 18-10 34-26 34-50V16z"/>
      <path d="M52 16L28 23v25c0 18 11 30 24 38"/>
      <path d="M36 52l12 12 22-26"/>
    </svg>
    <div class="num">02</div>
    <h3>Zertifiziert</h3>
    <p>Sie erhalten ein qualifiziertes<br>und belastbares Gutachten von einem<br>zertifizierten Sachverständigen<br>(höchste Akzeptanz bei allen<br>Parteien)</p>
  </div>

  <div class="reason" style="left:773px">
    <svg width="104" height="104" viewBox="0 0 104 104" fill="none" stroke="#1c1c1c" stroke-width="4" stroke-linecap="round" stroke-linejoin="round">
      <path d="M68 50V14L58 4H14v92h40"/><path d="M58 4v10h10"/>
      <path d="M24 22h26M24 32h34M24 42h34M24 52h18M24 62h14M24 72h14"/>
      <circle cx="66" cy="70" r="16"/><circle cx="66" cy="70" r="9"/><path d="M78 82l14 14"/>
    </svg>
    <div class="num">03</div>
    <h3>Verständlich</h3>
    <p>Ihr Gutachten wird für Sie logisch<br>und nachvollziehbar sein und kein<br>"Fachchinesisch" enthalten</p>
  </div>
</section>

<div class="faq-photo" role="img" aria-label="Photo of hands writing on financial charts next to a laptop"></div>
<section class="faq">
  <h2>FAQ</h2>
  <div class="body">
    <p>What are the buying motives of the customers?<br>Was sind die Kaufmotive der Kunden?</p>
    <p>- Sie wollen Anteile Ihres Unternehmens oder ihr gesamtes Unternehmen verkaufen?</p>
    <p>- Sie wollen Ihr Unternehmen auf Ihre Erben übertragen und benötigen eine Bewertung für das Finanzamt?</p>
    <p>- Sie müssen im Rahmen einer Trennung/Scheidung jemanden ausbezahlen und benötigen eine Bemessungsgrundlage?</p>
  </div>
</section>

<section class="statement" role="img" aria-label="Night skyline of a city with a TV tower by the river">
  <p style="top:96px">Lassen Sie Ihr Unternehmen von einem qualifizerten Sachverständigen bewerten<br>und gehen somit vielen (unnötigen) Streitereien aus dem Weg.</p>
  <p style="top:180px">Merke: Die Kosten für ein Gutachten sind immer überproportional günstiger als die<br>Kosten für Rechtsstreitigkeiten. Und das losgelöst von der psychischen Belastung<br>einer solchen Auseinandersetzung ...</p>
</section>

<section class="promise">
  <div class="brand-mark">LENZ HARWARD</div>
  <h2>Mein Qualitätsversprechen:</h2>
  <p>Sollte der avisierte Termin für die Erstellung des Gutachtens<br>überschritten werden, erhalten Sie das Gutachten absolut kostenfrei!<br>(Ich verzichte auf mein Honorar)</p>
</section>

<footer class="site-footer">
  <div class="footer-col" style="left:173px"><h4>Support</h4><ul><li>Sed ut perspiciatis</li><li>Unde omnis iste</li><li>Voluptatem</li><li>Accusantium</li><li>Doloremque</li><li>Laudantium</li></ul></div>
  <div class="footer-col" style="left:346px"><h4>Company</h4><ul><li>Sed ut perspiciatis</li><li>Unde omnis iste</li><li>Voluptatem</li><li>Accusantium</li><li>Doloremqu</li></ul></div>
  <div class="footer-col" style="left:517px"><h4>Links</h4><ul><li>Sed ut perspiciatis</li><li>Unde omnis iste</li><li>Voluptatem</li><li>Accusantium</li><li>Doloremque</li><li>Laudantium</li></ul></div>
  <div class="footer-col" style="left:707px"><h4>Newsletter</h4></div>
  <div class="signup"><div class="email">Email:</div><div class="btn">SIGN UP</div></div>
  <div class="follow">Follow us on <span class="dot"></span><span class="dot"></span></div>
  <div class="footer-rule"></div>
  <div class="copyright">© 2018 All Rights Are Reserved.Terms of Use | Privacy Policy</div>
</footer>

</body>
</html>
```